Stationery Design Project for Marketing Consultancy

I have started a new consultancy business and require the following elements to be designed using existing logo:
• Business card
• Letterhead
• Envelope (DL, C4, C5)
• Microsoft word template for report writing
• A4 Presentation Folder
• Powerpoint template
COPY FOR FRONT AND BACK OF BUSINESS CARD
logo
'Measurable Marketing. Epic Results' slogan (but no need to use existing lockup with logo)
name, B Bus. Mktg, Grad Dip Digital Mktg, CPM (post nominal abbreviations in smaller font)
mobile: 04XX-XXX-XXX (I will give details to the winner to add)
website: www.tolvarin.com.au
email: info@tolvarin.com.au
COPY FOR LETTERHEAD
Logo
Company Name
Please, submit your designs that include business card, letterhead and envelope. Once selected the winner will be asked to complete the project by creating the rest of the artwork.
FINAL FILES
Print ready files to be supplied as well as Indesign files so that minor amends can be made if necessary in future.
• Layered vectors in EPS & PDF
• Screen quality JPEG & PNGs
ABOUT THE BUSINESS: TOLVARIN
I work with clients to understand their business challenges, developing and executing measurable marketing strategies tied to key business metrics. Services include:
Services include:
• Business planning and business development
• Marketing and brand strategy
• Insight-driven integrated campaigns
• Loyalty programs and retention marketing
• Marketing automation
• Direct marketing (traditional and digital)
• Content strategy and development
Hi everyone,
Target Market(s)
Corporate decision makers (heads of marketing, general managers etc) and small to medium sized business owners. Predominately male aged 35+
Industry/Entity Type
Marketing
Requirements
Must have
- BRAND PERSONALITY
The successful design will communicate brand personality. I am a professional, results-driven entrepreneur, but want to show off my creative flair.
MEMORABILITY
Looking for a unique and eye-catching design. Am considering special printing effects (die cuts, letterpress, interactive elements, embossing, foiling etc) or a striking minimalist approach.
Nice to have
- I have a mission that could be incorporated on reverse if room -
Turning insights into actions & passion into profit.
Should not have
- Use of pink or green.

```html
<!DOCTYPE html>
<html lang="en">
<head>
<meta charset="utf-8">
<title>Tolvarin Letterhead</title>
<link rel="stylesheet" href="https://fonts.googleapis.com/css2?family=Open+Sans:wght@400;700;800&family=Questrial&display=swap">
<style>
  :root {
    --backdrop: #e4e4e4;
    --paper: #f6f6f6;
    --brand-blue: #1d7fa6;
    --brand-deep: #1f4f7a;
    --band-light: #1690b8;
    --band-dark: #1d5c88;
    --band-text: #d9ecf5;
  }
  * { box-sizing: border-box; margin: 0; padding: 0; }
  html, body {
    width: 1200px;
    height: 968px;
    overflow: hidden;
    background: var(--backdrop);
  }
  .letterhead {
    position: absolute;
    left: 282px;
    top: 30px;
    width: 636px;
    height: 900px;
    background: var(--paper);
    box-shadow: 0 2px 10px rgba(0,0,0,0.12);
  }
  .masthead {
    position: absolute;
    top: 70px;
    left: 0;
    width: 100%;
    text-align: center;
  }
  .masthead__mark {
    display: block;
    width: 34px;
    height: 34px;
    margin: 0 auto 10px;
    border-radius: 50%;
    background: var(--brand-blue);
  }
  .masthead__name {
    font-family: "Open Sans", sans-serif;
    font-weight: 800;
    font-size: 30px;
    letter-spacing: 1px;
    color: var(--brand-deep);
    line-height: 1;
  }
  .masthead__slogan {
    margin-top: 5px;
    font-family: "Open Sans", sans-serif;
    font-weight: 700;
    font-size: 9px;
    letter-spacing: 0.6px;
    color: var(--brand-blue);
  }
  .contact-band {
    position: absolute;
    left: 0;
    bottom: 0;
    width: 100%;
    height: 96px;
    background: linear-gradient(180deg, var(--band-light) 0%, var(--band-dark) 100%);
  }
  .contact-band__mark {
    position: absolute;
    left: 26px;
    top: 18px;
    width: 22px;
    height: 22px;
    border-radius: 50%;
    background: #ffffff;
  }
  .contact-list {
    position: absolute;
    left: 110px;
    right: 30px;
    bottom: 22px;
    display: flex;
    justify-content: space-between;
    list-style: none;
  }
  .contact-list__item {
    display: flex;
    align-items: center;
    gap: 8px;
    font-family: "Questrial", sans-serif;
    font-size: 12px;
    color: var(--band-text);
    white-space: nowrap;
  }
  .contact-list__icon {
    width: 14px;
    height: 14px;
    flex: none;
  }
</style>
</head>
<body>
  <main class="letterhead">
    <header class="masthead">
      <span class="masthead__mark"></span>
      <div class="masthead__name">TOLVARIN</div>
      <div class="masthead__slogan">CLEAR STRATEGY. STRONGER GROWTH.</div>
    </header>

    <footer class="contact-band">
      <span class="contact-band__mark"></span>
      <ul class="contact-list">
        <li class="contact-list__item">
          <svg class="contact-list__icon" viewBox="0 0 14 14" aria-hidden="true">
            <circle cx="7" cy="7" r="6.3" fill="none" stroke="#d9ecf5" stroke-width="1"/>
            <path d="M5 3.8 L6.2 5.2 L5.6 6 Q6.3 7.6 8 8.4 L8.8 7.8 L10.2 9 L9.4 10.2 Q6.6 10 4 5 Z" fill="#d9ecf5"/>
          </svg>
          +0491-570-156
        </li>
        <li class="contact-list__item">
          <svg class="contact-list__icon" viewBox="0 0 14 14" aria-hidden="true">
            <circle cx="7" cy="7" r="6.3" fill="none" stroke="#d9ecf5" stroke-width="1"/>
            <rect x="3.8" y="4.8" width="6.4" height="4.4" fill="none" stroke="#d9ecf5" stroke-width="0.9"/>
            <path d="M3.8 4.8 L7 7.3 L10.2 4.8" fill="none" stroke="#d9ecf5" stroke-width="0.9"/>
          </svg>
          info@tolvarin.com.au
        </li>
        <li class="contact-list__item">
          <svg class="contact-list__icon" viewBox="0 0 14 14" aria-hidden="true">
            <circle cx="7" cy="7" r="6.3" fill="none" stroke="#d9ecf5" stroke-width="1"/>
            <circle cx="7" cy="7" r="3.4" fill="none" stroke="#d9ecf5" stroke-width="0.8"/>
            <ellipse cx="7" cy="7" rx="1.4" ry="3.4" fill="none" stroke="#d9ecf5" stroke-width="0.8"/>
            <line x1="3.6" y1="7" x2="10.4" y2="7" stroke="#d9ecf5" stroke-width="0.8"/>
          </svg>
          www.tolvarin.com.au
        </li>
      </ul>
    </footer>
  </main>
</body>
</html>
```